Harbor Ledger Funds Bus card and Logo

I need a logo design and Bus card design. The fund focuses on evaluating and investing in minerals (sub-surface rights) and real estate.

Harbor ledger refers to a book of knowledge that each plebe gets when entering the Kelmont Marine Academy (my alma mater)

Target Market(s)

Investors and financial advisors

Contact Information for Business Card

Simple - perhaps a logo with a theme on book of knowledge

Logo Text

Ex Scientia Imperium

Font styles to use
Serif
Sans Serif

Colors

Designer to choose colors to be used in the design.

Requirements
Must have
• memorable logo that is relatively simple

```html
<!DOCTYPE html>
<html lang="en">
<head>
<meta charset="utf-8">
<title>Harbor Ledger Funds – Business Card</title>
<link rel="stylesheet" href="https://fonts.googleapis.com/css2?family=Arimo:wght@400;700&display=swap">
<style>
  :root {
    --backdrop: #e9ebee;
    --card-white: #ffffff;
    --card-shade: #f1f2f4;
    --brand-blue: #1fa9d8;
    --brand-blue-light: #2cc3e8;
    --brand-blue-deep: #168fc0;
    --band-grey: #a4a7ab;
    --text-grey: #6d7074;
    --text-light: #ffffff;
  }
  * { box-sizing: border-box; margin: 0; padding: 0; }
  html, body {
    width: 1200px;
    height: 780px;
    overflow: hidden;
    background: var(--backdrop);
    font-family: "Arimo", Arial, sans-serif;
  }
  .canvas {
    position: relative;
    width: 1200px;
    height: 780px;
  }
  .business-card {
    position: absolute;
    left: 100px;
    top: 104px;
    width: 1000px;
    height: 572px;
    border-radius: 34px;
    overflow: hidden;
    background: linear-gradient(135deg, var(--card-white) 0%, var(--card-shade) 100%);
    box-shadow: 0 18px 40px rgba(0, 0, 0, 0.18);
  }
  .wave-bands {
    position: absolute;
    inset: 0;
    width: 100%;
    height: 100%;
  }
  .brand-lockup {
    position: absolute;
    left: 80px;
    top: 200px;
    display: flex;
    align-items: center;
    gap: 28px;
  }
  .brand-square {
    width: 70px;
    height: 70px;
    background: var(--brand-blue);
  }
  .brand-divider {
    width: 2px;
    height: 120px;
    background: var(--band-grey);
  }
  .brand-name {
    font-weight: 700;
    font-size: 38px;
    line-height: 1.08;
    letter-spacing: 3px;
    text-transform: uppercase;
    color: var(--text-grey);
  }
  .contact-block {
    position: absolute;
    left: 470px;
    top: 380px;
    color: var(--text-light);
  }
  .person-name {
    font-weight: 700;
    font-size: 30px;
    letter-spacing: 0.5px;
    text-transform: uppercase;
  }
  .person-title {
    font-size: 20px;
    margin-bottom: 22px;
  }
  .contact-line {
    display: flex;
    align-items: center;
    gap: 12px;
    font-size: 21px;
    line-height: 1.5;
  }
  .contact-icon {
    width: 18px;
    height: 18px;
    flex: none;
  }
  .address-block {
    position: absolute;
    right: 50px;
    top: 240px;
    text-align: right;
    color: var(--text-light);
    font-size: 18px;
    line-height: 1.4;
    white-space: nowrap;
  }
</style>
</head>
<body>
<main class="canvas">
  <section class="business-card" aria-label="Harbor Ledger Funds business card">
    <svg class="wave-bands" viewBox="0 0 1000 572" preserveAspectRatio="none" aria-hidden="true">
      <defs>
        <linearGradient id="blueWave" x1="0" y1="1" x2="1" y2="0">
          <stop offset="0" stop-color="var(--brand-blue-deep)"/>
          <stop offset="0.5" stop-color="var(--brand-blue-light)"/>
          <stop offset="1" stop-color="var(--brand-blue-deep)"/>
        </linearGradient>
      </defs>
      <path class="grey-band" fill="var(--band-grey)"
            d="M 250 572 C 330 440, 450 330, 560 250 C 660 175, 700 80, 700 0 L 1000 0 L 1000 572 Z"/>
      <path class="white-rule" fill="var(--card-white)"
            d="M 300 572 C 380 440, 500 340, 610 265 C 710 195, 760 90, 780 0 L 1000 0 L 1000 572 Z"/>
      <path class="blue-band" fill="url(#blueWave)"
            d="M 312 572 C 392 442, 512 344, 622 270 C 722 200, 775 95, 796 0 L 1000 0 L 1000 572 Z"/>
    </svg>

    <div class="brand-lockup">
      <div class="brand-square"></div>
      <div class="brand-divider"></div>
      <div class="brand-name">Harbor<br>Ledger<br>Funds LLC</div>
    </div>

    <div class="address-block">
      <p>PO BOX 418, Quayside Lane</p>
      <p>2nd street Portmere</p>
    </div>

    <div class="contact-block">
      <p class="person-name">Dana Whitlock</p>
      <p class="person-title">President</p>
      <p class="contact-line">
        <svg class="contact-icon" viewBox="0 0 18 18" aria-hidden="true">
          <rect x="4" y="1" width="10" height="16" rx="2" fill="none" stroke="#fff" stroke-width="1.6"/>
          <circle cx="9" cy="14" r="1" fill="#fff"/>
        </svg>
        <span>555 014 2290</span>
      </p>
      <p class="contact-line">
        <svg class="contact-icon" viewBox="0 0 18 18" aria-hidden="true">
          <rect x="1" y="3" width="16" height="12" rx="1" fill="#fff"/>
          <path d="M1 4 L9 10 L17 4" fill="none" stroke="var(--brand-blue-deep)" stroke-width="1.4"/>
        </svg>
        <span>info@harborledgerfunds.com</span>
      </p>
    </div>
  </section>
</main>
</body>
</html>
```